Luxury Wine Label for New Startup Winery

We need a wine label for our new winery startup. We have worked with a local designer but do not feel the resulting label / logo have the elevation required to present our brand as a luxury wine. Our winery is called "Quailbrook Vineyards" and we are focused on extremely high quality hand crafted artisan and estate wines from the Pacific Northwest.
We would like to see designs that utilize a tree line, or other imagery that represents the "Quailbrook" part of our company name. Another interesting feature could be wood grain.
A logo will be required based on your design so please design with this in mind:
This logo should be consistent with the wine bottle label design, and should be representative of our high end exclusive wine while giving a sense of place (Oregon/ Pacific Northwest.)
I will supply an image of the design we received from our local designer, PLEASE NOTE: in general we do like wood grain and tree line concepts but feel the execution was poorly done.
ATTN: Logo design should be suitable for use on: Bottles (Red wine/rose/white wine), Bussiness cards, vehicle signage, business signage, etc
P.S.:
If you have a design that is not outside the box we are still interested in seeing it.
Label is for a burgundy style bottle with a label height of 3.5 - 4" and a width of 3.5-4"
any label <= 4"x4" and >=3.5"x3.5" will be acceptable:
HOWEVER Width should be greater than or equal to height due to the bottle format
Target Market(s)
Wine enthusiasts with adequate discretionary budgets to afford $100 bottles of wine.
Industry/Entity Type
Wine / Winery
Requirements
Must have
- A sense of luxury, a feel of exclusivity, and a theme consistent with our product and brand name
Nice to have
- Tree line, wood grain or other wood themes. Serif fonts
Should not have
- anything cheesy, off topic, hard to read script fonts or anything that makes the label hard to read from a few feet away or too busy

```html
<!DOCTYPE html>
<html lang="en">
<head>
<meta charset="utf-8">
<title>Quailbrook Vineyards – 2024 Pinot Noir Label</title>
<link rel="stylesheet" href="https://fonts.googleapis.com/css2?family=Tinos&display=swap">
<style>
  :root {
    --page-bg: #ffffff;
    --label-dark: #35343f;
    --label-mid: #4a4956;
    --label-light: #5d5c69;
    --ink-wordmark: #8f8e99;
    --ink-text: #a3a2ad;
    --gold-deep: #c9961f;
    --gold-light: #f0c04a;
  }
  * { margin: 0; padding: 0; box-sizing: border-box; }
  html, body {
    width: 1200px;
    height: 1200px;
    overflow: hidden;
    background: var(--page-bg);
  }
  .canvas {
    position: relative;
    width: 1200px;
    height: 1200px;
  }
  .wine-label {
    position: absolute;
    left: 150px;
    top: 170px;
    width: 900px;
    height: 860px;
    border-radius: 10px;
    background: linear-gradient(90deg, var(--label-dark) 0%, var(--label-mid) 55%, var(--label-light) 100%);
    font-family: "Tinos", "Times New Roman", serif;
    font-weight: 400;
    color: var(--ink-text);
  }
  .wine-label h1,
  .wine-label h2 { font-weight: 400; }
  .winery-name {
    position: absolute;
    left: 56px;
    bottom: 250px;
    writing-mode: vertical-rl;
    transform: rotate(180deg);
    font-size: 84px;
    line-height: 0.9;
    letter-spacing: -1px;
    color: var(--ink-wordmark);
    text-transform: uppercase;
    white-space: nowrap;
  }
  .crest-area {
    position: absolute;
    left: 415px;
    top: 120px;
    width: 290px;
    height: 270px;
    border-radius: 6px;
    background: radial-gradient(ellipse at center, var(--gold-light) 0%, var(--gold-deep) 70%, rgba(201,150,31,0.6) 100%);
  }
  .vintage-block {
    position: absolute;
    left: 360px;
    width: 400px;
    text-align: center;
  }
  .vintage-year {
    top: 480px;
    font-size: 52px;
    line-height: 1;
  }
  .varietal {
    top: 545px;
    font-size: 70px;
    line-height: 1;
  }
  .appellation {
    position: absolute;
    left: 140px;
    width: 700px;
    top: 680px;
    text-align: center;
    font-size: 34px;
    line-height: 1;
  }
  .alcohol {
    position: absolute;
    left: 140px;
    width: 700px;
    top: 752px;
    text-align: center;
    font-size: 34px;
    line-height: 1;
  }
</style>
</head>
<body>
  <main class="canvas">
    <section class="wine-label">
      <h1 class="winery-name">Quailbrook<br>Vineyards</h1>
      <div class="crest-area" role="img" aria-label="Gold ornamental crest emblem"></div>
      <p class="vintage-block vintage-year">2024</p>
      <h2 class="vintage-block varietal">Pinot Noir</h2>
      <p class="appellation">Willamette Valley, Oregon</p>
      <p class="alcohol">14.2% by Vol.</p>
    </section>
  </main>
</body>
</html>
```